Website redesign for job agency recruitment

Please refer to the attached document, “Tarvenly Work Website Brief,” for comprehensive details regarding the scope, objectives, and requirements of this website redesign project.

For imagery you can use images from this website https://www.pixelmarrowfoto.com or any other you regularly use.

Target Market(s)

Jobseekers and Companies looking for general labour

Industry/Entity Type

Services: Oil, Gas and Mining, Administrative, Construction and Trades, Warehouse and Logistics and, Manufacturing.

Number of Pages Required

5+ page

Font styles to use
Serif
Other font styles liked:
• Inter, Open-Sans or similar.

Requirements
Must have
• The requirements highlighted in the Word document attached. The final design needs to be provided in Figma including all viewports (Desktop, mobiel and tablet)
Should not have
• Website we like as a reference: www.brevicktalentco.com, www.qelvaworks.com, www.zunmarra.com, www.ferrowhires.com, www.9vtalentpool.com, www.hiringwithtrello.ca

```html
<!DOCTYPE html>
<html lang="en">
<head>
<meta charset="utf-8">
<title>Tarvenly Work Agency Ltd. — Home</title>
<link href="https://fonts.googleapis.com/css2?family=Manrope:wght@400;500;600;700;800&display=swap" rel="stylesheet">
<style>
:root{
  --navy:#0d3a9b;
  --blue:#1f56c0;
  --sky:#0d96db;
  --gold:#f2bd18;
  --ink:#111111;
  --white:#ffffff;
  --footer:#000000;
  --muted:#555b66;
}
*{margin:0;padding:0;box-sizing:border-box}
html,body{width:1200px;height:3200px;overflow:hidden}
body{position:relative;font-family:"Manrope",sans-serif;color:var(--ink);background:var(--white)}
.abs{position:absolute}
.topbar{left:0;top:0;width:1200px;height:40px;background:var(--navy);color:var(--white);font-size:14px;font-weight:600}
.topbar .toll{position:absolute;left:151px;top:11px}
.topbar .dot{position:absolute;top:8px;width:25px;height:25px;border-radius:50%;background:var(--gold)}
.header{left:0;top:40px;width:1200px;height:113px;background:var(--white)}
.brand{position:absolute;left:151px;top:36px;display:flex;align-items:center;gap:14px}
.brand .mark{font-size:34px;font-weight:800;color:var(--navy)}
.brand .name{font-size:14px;font-weight:700;color:var(--navy);line-height:1.2}
.brand .name small{display:block;font-size:9px;font-weight:500;color:var(--muted)}
.nav a{position:absolute;top:50px;font-size:15.5px;font-weight:500;color:var(--ink);text-decoration:none}
.nav a.active{color:var(--navy)}
.hero{left:0;top:153px;width:1200px;height:600px;background:linear-gradient(180deg,#2b3744 0%,#3c4652 30%,#7a6241 62%,#c79a55 78%,#4a3a2a 100%)}
.hero-text{left:0;top:310px;width:1200px;text-align:center;color:var(--white)}
.hero-text h1{font-size:50px;font-weight:700;letter-spacing:-0.5px}
.hero-text p{margin:12px auto 0;width:520px;font-size:16px;font-weight:500;line-height:22px}
.btn{position:absolute;height:40px;border-radius:20px;font-size:14.5px;font-weight:700;display:flex;align-items:center;justify-content:center;gap:7px}
.btn .arr{width:12px;height:12px;border-radius:50%;display:inline-block}
.btn-navy{background:var(--navy);color:var(--white)}
.btn-navy .arr{background:var(--white)}
.btn-gold{background:var(--gold);color:var(--navy)}
.btn-gold .arr{background:var(--navy)}
.services{left:0;top:733px;width:1200px;height:857px;background:radial-gradient(circle at 1050px 80px,#dfe7f3 0,#f4f5f7 30%,rgba(255,255,255,0) 55%),radial-gradient(circle at 80px 700px,#e8e6dc 0,rgba(255,255,255,0) 35%),#f7f8fa}
.badge{font-size:17px;font-weight:800;color:var(--navy);text-align:center;width:100%}
.section-title{font-size:40px;font-weight:500;text-align:center;width:100%;letter-spacing:-0.5px}
.section-title b{font-weight:800}
.svc-label{font-size:18.5px;font-weight:500;color:var(--ink)}
.svc-label::after{content:"»";margin-left:10px;font-size:16px}
.card{left:620px;top:1031px;width:244px;height:236px;background:var(--sky);border-radius:70px 0 0 0;color:var(--white);padding:40px 28px 0 55px}
.card h3{font-size:17px;font-weight:600;margin-bottom:14px}
.card p{font-size:15px;line-height:22.5px}
.card .more{margin-top:18px;font-size:15px;font-weight:500}
.about{left:0;top:1590px;width:1200px;height:693px;background:linear-gradient(90deg,#1f56c0 0%,#1f56c0 60%,#2a59b0 80%,#22509f 100%)}
.about-copy{left:653px;top:1718px;width:397px;color:var(--white)}
.about-copy .tag{font-size:17px;font-weight:800}
.about-copy h2{font-size:40px;font-weight:700;margin:24px 0 18px;letter-spacing:-0.5px}
.about-copy p{font-size:13.5px;line-height:22.5px;text-align:justify;margin-bottom:22px}
.about-photo{left:139px;top:1705px;width:460px;height:460px;border-radius:50%;border:7px solid var(--gold);background:linear-gradient(180deg,#5e9ed0 0%,#a9cbe4 35%,#9aa3ad 60%,#4a5560 85%,#c4a05a 100%)}
.connect-bg{left:0;top:2283px;width:1200px;height:560px;background:radial-gradient(circle at 1050px 80px,#dfe7f3 0,rgba(255,255,255,0) 40%),radial-gradient(circle at 80px 400px,#e8e6dc 0,rgba(255,255,255,0) 35%),#f7f8fa}
.connect-sub{font-size:16px;text-align:center;width:100%;font-weight:500}
.footer-text{color:var(--white)}
.foot-col h4{font-size:19px;font-weight:500}
.foot-col .rule{width:30px;height:2px;background:var(--white);margin:10px 0 12px}
.foot-col a{display:block;color:var(--white);font-size:12.5px;text-decoration:none;line-height:26px}
.contact-item{font-size:12.5px;line-height:19px}
.contact-item .lbl{display:block;margin-bottom:3px}
</style>
</head>
<body>

<div class="abs topbar">
  <span class="toll">Toll Free: 1-888-555-0142</span>
  <span class="dot" style="left:989px"></span>
  <span class="dot" style="left:1023px"></span>
</div>

<header class="abs header">
  <div class="brand">
    <span class="mark">TWA</span>
    <span class="name">Tarvenly Work Agency Ltd.<small>The right people to power your business</small></span>
  </div>
  <nav class="nav">
    <a class="active" style="left:461px">Home</a>
    <a style="left:535px">Candidates</a>
    <a style="left:648px">Companies</a>
    <a style="left:761px">About Us</a>
    <a style="left:860px">Contact</a>
    <a style="left:949px">Forms &amp; Links</a>
  </nav>
</header>

<div class="abs hero" role="img" aria-label="City skyline of tall office towers at sunset"></div>

<div class="abs services" role="img" aria-label="Faint background of workers and welding sparks"></div>

<svg class="abs" style="left:0;top:560px" width="1200" height="200" viewBox="0 0 1200 200">
  <path d="M0 18 Q600 240 1200 18 L1200 200 L0 200 Z" fill="#f4f5f7"/>
  <path d="M0 18 Q600 240 1200 18 Q600 190 0 18 Z" fill="#f2bd18"/>
</svg>

<div class="abs hero-text">
  <h1>Our Goal is Your Success</h1>
  <p>We Know That The Success Of Every Business Relies Upon Having The Finest Employees.</p>
</div>
<div class="btn btn-navy" style="left:417px;top:437px;width:169px">For Candidates <span class="arr"></span></div>
<div class="btn btn-gold" style="left:601px;top:437px;width:169px">For Employers <span class="arr"></span></div>

<div class="abs badge" style="left:0;top:832px">TWA</div>
<h2 class="abs section-title" style="left:0;top:872px">OUR <b>SERVICES</b></h2>

<svg class="abs" style="left:0;top:980px" width="420" height="470" viewBox="0 980 420 470">
  <circle cx="149" cy="1211" r="224" fill="none" stroke="#0d96db" stroke-width="10" stroke-dasharray="704 704" transform="rotate(-90 149 1211)"/>
  <circle cx="149" cy="1211" r="224" fill="none" stroke="#f2bd18" stroke-width="10" stroke-dasharray="0 98 90 145 59 156 156 703" transform="rotate(-90 149 1211)"/>
  <text x="228" y="1222" text-anchor="middle" font-family="Manrope, sans-serif" font-size="62" font-weight="800" fill="#0d3a9b">TWA</text>
</svg>

<span class="abs svc-label" style="left:308px;top:986px">Oil</span>
<span class="abs svc-label" style="left:373px;top:1041px">Gas and Mining</span>
<span class="abs svc-label" style="left:411px;top:1131px">Administrative</span>
<span class="abs svc-label" style="left:411px;top:1218px">Administrative</span>
<span class="abs svc-label" style="left:375px;top:1304px">Gas and Mining</span>
<span class="abs svc-label" style="left:308px;top:1394px">Oil</span>

<svg class="abs" style="left:898px;top:990px" width="152" height="147" role="img" aria-label="Two workers in blue overalls at an industrial plant">
  <defs><linearGradient id="plantTone" x1="0" y1="0" x2="1" y2="1"><stop offset="0" stop-color="#9aa6b4"/><stop offset="0.55" stop-color="#5f6e80"/><stop offset="1" stop-color="#2c5aa8"/></linearGradient></defs>
  <path d="M0 0 H80 A72 72 0 0 1 152 72 V147 H0 Z" fill="url(#plantTone)"/>
</svg>
<div class="abs" style="left:806px;top:1149px;width:244px;height:236px;background:linear-gradient(170deg,#1f6fa8 0%,#2f5b80 40%,#3b4658 70%,#c99a5a 100%)" role="img" aria-label="Aerial view of oil storage tanks at a harbour"></div>

<div class="abs card">
  <h3>Oil</h3>
  <p>Lorem ipsum dolor sit amet, consectetur adipiscing elit, sed do eiusmod tempor</p>
  <div class="more">Learn More &nbsp;»</div>
</div>

<section class="abs about"></section>
<div class="abs about-photo" role="img" aria-label="Engineer in hard hat checking pipelines at a refinery"></div>

<div class="abs about-copy">
  <div class="tag">TWA</div>
  <h2>ABOUT US</h2>
  <p>Tarvenly Work Agency offers a complete range of staffing services to keep pace with your career or operational demands. We understand it's not only daunting but very costly in both time and money to make your business thrive in a rapidly changing environment.</p>
  <p>Our staffing and recruitment services are not just limited to finding good people. We are a Canada-wide team of capable search specialists, career counselors, HR specialists, and business consultants who enjoy providing our clients with a very customized staffing solution</p>
</div>
<div class="btn btn-gold" style="left:653px;top:2112px;width:170px">Read More <span class="arr"></span></div>

<div class="abs connect-bg" role="img" aria-label="Faint background of workers and welding sparks"></div>
<div class="abs badge" style="left:0;top:2369px">TWA</div>
<h2 class="abs section-title" style="left:0;top:2425px">CONNECT <b>WITH US</b></h2>
<p class="abs connect-sub" style="left:0;top:2490px">Learn more about our services and what we can do for your company</p>
<div class="btn btn-navy" style="left:515px;top:2543px;width:169px">Get In Touch <span class="arr"></span></div>

<svg class="abs" style="left:0;top:2660px" width="1200" height="540" viewBox="0 0 1200 540">
  <path d="M0 172 Q600 -60 1200 172 L1200 540 L0 540 Z" fill="#000"/>
  <path d="M0 172 Q600 -60 1200 172 Q600 -20 0 172 Z" fill="#f2bd18"/>
</svg>

<div class="abs footer-text" style="left:176px;top:2898px;width:240px;font-size:68px;font-weight:800;text-align:center;line-height:1">TWA</div>
<div class="abs footer-text" style="left:176px;top:3005px;width:260px">
  <div style="font-size:19px;font-weight:500">Tarvenly Work Agency Ltd.</div>
  <div style="font-size:12px;margin-top:6px">The right people to power your business</div>
</div>

<div class="abs foot-col footer-text" style="left:489px;top:2855px">
  <h4>More Info</h4><div class="rule"></div>
  <a>Home</a><a>Candidates</a><a>Companies</a><a>About Us</a><a>Contact</a><a>Forms &amp; Links</a>
</div>
<div class="abs foot-col footer-text" style="left:678px;top:2855px">
  <h4>More Info</h4><div class="rule"></div>
  <a>Terms &amp; Conditions</a><a>Privacy Policy</a><a>About Us</a><a>Support</a>
</div>
<div class="abs foot-col footer-text" style="left:882px;top:2853px;width:160px">
  <h4>Contact Us</h4><div class="rule"></div>
  <div class="contact-item"><span class="lbl">ADDRESS</span>
    <svg width="9" height="11" viewBox="0 0 9 11"><path d="M4.5 0A4.5 4.5 0 0 0 0 4.5C0 8 4.5 11 4.5 11S9 8 9 4.5A4.5 4.5 0 0 0 4.5 0Z" fill="#fff"/></svg>
    Lorem ipsum dolor sit amet, consectetur</div>
  <div class="contact-item" style="margin-top:14px"><span class="lbl">PHONE</span>
    <svg width="10" height="10" viewBox="0 0 10 10"><path d="M2 0L4 2.5 3 4Q4.5 6.5 6 7L7.5 6 10 8 8.5 10Q3 9.5 0 1.5Z" fill="#fff"/></svg>
    +1-888-555-0142</div>
  <div class="contact-item" style="margin-top:16px"><span class="lbl">EMAIL</span>
    <svg width="11" height="8" viewBox="0 0 11 8"><rect width="11" height="8" rx="1" fill="#fff"/><path d="M0 0L5.5 4.5 11 0" stroke="#000" fill="none"/></svg>
    info@tarvenlywork.com</div>
</div>

<div class="abs" style="left:176px;top:3084px;width:855px;height:1px;background:#777"></div>
<div class="abs footer-text" style="left:0;top:3129px;width:1200px;text-align:center;font-size:13.5px;font-weight:600">© copyrights 2026 Tarvenly Work Agency Ltd I Rights Reserved</div>

</body>
</html>
```